Facebook post - Kestrel Bay Finishes has arrived to make your tiles smile!

Kestrel Bay Finishes would like to release a Facebook post calling out to the market that we have arrived. The company has a new and fresh branding aiming for a female demographic between the ages of 40 and 55 located in the South West of Western Australia. The company image MUST be centered around trust! Our Primary aim is to create an uncompromising trust from the very first impression. Our logo tag line is, 'We love to make your tiles smile'.
I need 5 x facebook template designs and also 5 x posts.
Our 1st campaign is to be 5 x posts centered around the arrival of this fantastic new company.
We are company that provides the services of:
- Grout and silicone repair.
- Broken or drummy tile replacement and;
- Grout sealing
Dont forget that we must communicate TRUST and the we love to make your tiles SMILE!

```html
<!DOCTYPE html>
<html lang="en">
<head>
<meta charset="utf-8">
<title>Kestrel Bay Finishes – We love to make your tiles smile</title>
<link href="https://fonts.googleapis.com/css2?family=Oswald:wght@300;400&display=swap" rel="stylesheet">
<style>
  :root {
    --tile-white: #ffffff;
    --grout: #d6d7d9;
    --grout-shadow: #e9eaeb;
    --brand-blue: #2fa8da;
    --ink-grey: #4a4a4c;
  }
  html, body {
    margin: 0;
    padding: 0;
    width: 1200px;
    height: 1200px;
    overflow: hidden;
    background: var(--tile-white);
  }
  .post {
    position: relative;
    width: 1200px;
    height: 1200px;
    overflow: hidden;
    font-family: "Oswald", "Arial Narrow", sans-serif;
  }
  .tile-wall {
    position: absolute;
    inset: 0;
    width: 1200px;
    height: 1200px;
  }
  .brand-name {
    position: absolute;
    left: 120px;
    top: 560px;
    width: 420px;
    margin: 0;
    transform: skewY(-19deg);
    transform-origin: 0 0;
    color: var(--brand-blue);
    font-weight: 300;
    font-size: 50px;
    line-height: 1.1;
    letter-spacing: 0.12em;
    text-transform: uppercase;
  }
  .tagline {
    position: absolute;
    left: 680px;
    top: 375px;
    margin: 0;
    transform: skewY(-19deg);
    transform-origin: 0 0;
    font-weight: 300;
    text-transform: uppercase;
    letter-spacing: 0.2em;
    white-space: nowrap;
  }
  .tagline span {
    display: block;
  }
  .tagline .line-lead {
    font-size: 108px;
    line-height: 108px;
  }
  .tagline .line-small {
    font-size: 81px;
    line-height: 82px;
  }
  .tagline .accent {
    color: var(--brand-blue);
  }
  .tagline .muted {
    color: var(--ink-grey);
  }
  .tagline .line-smile {
    margin-top: 63px;
    font-size: 133px;
    line-height: 133px;
    letter-spacing: 0.1em;
    color: var(--brand-blue);
  }
</style>
</head>
<body>
  <main class="post">
    <svg class="tile-wall" viewBox="0 0 1200 1200" aria-hidden="true">
      <defs>
        <linearGradient id="tile-edge" x1="0" y1="0" x2="1" y2="1">
          <stop offset="0" stop-color="#ffffff"/>
          <stop offset="1" stop-color="#f7f7f8"/>
        </linearGradient>
        <pattern id="tile-grid" patternUnits="userSpaceOnUse"
                 x="44" y="-45" width="561" height="500"
                 patternTransform="skewY(-19)">
          <rect x="0" y="0" width="561" height="500" fill="var(--grout)"/>
          <rect x="2" y="2" width="557" height="496" fill="var(--grout-shadow)"/>
          <rect x="6" y="6" width="549" height="488" rx="3" fill="url(#tile-edge)"/>
        </pattern>
      </defs>
      <rect class="tile-surface" x="0" y="0" width="1200" height="1200" fill="url(#tile-grid)"/>
    </svg>

    <p class="brand-name">Kestrel Bay<br>Finishes</p>

    <h1 class="tagline">
      <span class="line-lead accent">We love</span>
      <span class="line-lead muted">to make</span>
      <span class="line-small muted">your tiles</span>
      <span class="line-smile">Smile!</span>
    </h1>
  </main>
</body>
</html>
```